Duct Manufacturing Company new to the industry needs business card and stationary design

we are sheet metal duct manufacturers looking for a business card design to fit my new business logo.
nothing to crazy that will date, but want it to stand out from the crowed.
I'm sure you guys will work it out.

Contact Information for Business Card

Glen Marsh
Director

Address
17 Dorwell St
Kelbrook NSW 2715

0438 760 514

Sales@flowbend.com.au

Font styles to use
Other font styles liked:
• BankGothic md bt

Requirements
Nice to have
• Like the idea of corner rounded to match logo
• like to keep colours flowing
• font I like sharp square not rounded

```html
<!DOCTYPE html>
<html lang="en">
<head>
<meta charset="utf-8">
<title>Flowbend Industries – Business Card</title>
<link href="https://fonts.googleapis.com/css2?family=Michroma&family=Montserrat:wght@400;500&display=swap" rel="stylesheet">
<style>
  :root {
    --page-bg: #e4e4e4;
    --card-black: #0d0d0d;
    --card-black-soft: #2a2a2a;
    --card-white: #ffffff;
    --brand-blue: #1a5fb0;
    --brand-blue-dark: #0d4a94;
    --brand-green: #8cc63f;
    --brand-green-dark: #7ab533;
    --text-dark: #3a3a3a;
    --text-muted: #6a6a6a;
    --divider: #e2e2e2;
  }
  * { margin: 0; padding: 0; box-sizing: border-box; }
  html, body { width: 1200px; height: 1200px; overflow: hidden; }
  body {
    background: var(--page-bg);
    position: relative;
    font-family: "Montserrat", Arial, sans-serif;
  }
  .card {
    position: absolute;
    left: 250px;
    width: 700px;
    height: 400px;
    border-radius: 26px;
    overflow: hidden;
    box-shadow: 0 8px 22px rgba(0,0,0,0.18);
  }
  .card--front {
    top: 150px;
    background: linear-gradient(115deg, var(--card-black) 0%, var(--card-black-soft) 45%, var(--card-black) 70%);
    display: flex;
    align-items: center;
    justify-content: center;
  }
  .card--back { top: 650px; background: var(--card-white); }

  .wordmark {
    display: flex;
    align-items: center;
    gap: 16px;
    font-family: "Michroma", "Arial Black", sans-serif;
    color: var(--brand-green);
    text-transform: uppercase;
  }
  .wordmark__dot {
    width: 44px; height: 44px; border-radius: 50%;
    background: var(--brand-blue);
    flex: none;
  }
  .wordmark__name { font-size: 34px; line-height: 1.15; letter-spacing: 1px; }
  .wordmark__name span { display: block; }

  .card--back .wordmark { position: absolute; left: 40px; top: 130px; }
  .card--back .wordmark__dot { width: 36px; height: 36px; }
  .card--back .wordmark__name { font-size: 27px; }

  .card__divider {
    position: absolute; left: 360px; top: 30px;
    width: 1px; height: 250px; background: var(--divider);
  }
  .contact { position: absolute; left: 392px; top: 60px; }
  .contact__name {
    font-family: "Michroma", "Arial Black", sans-serif;
    font-size: 22px; font-weight: 400; color: var(--brand-blue); letter-spacing: 1px;
    text-transform: uppercase;
  }
  .contact__role { font-size: 13px; color: var(--text-muted); margin: 4px 0 22px; }
  .contact__list { list-style: none; font-size: 15px; color: var(--text-dark); line-height: 1.6; }
  .contact__item { display: flex; align-items: center; gap: 10px; }
  .contact__item--plain { padding-left: 24px; }
  .contact__icon { width: 14px; height: 14px; flex: none; fill: var(--brand-blue); }

  .bands { position: absolute; left: 0; bottom: 0; width: 700px; height: 90px; }
  .website {
    position: absolute; right: 34px; bottom: 22px;
    font-size: 15px; color: var(--card-white); letter-spacing: 0.5px;
  }
</style>
</head>
<body>

<section class="card card--front" aria-label="Card front">
  <div class="wordmark">
    <div class="wordmark__dot"></div>
    <div class="wordmark__name"><span>Flowbend</span><span>Industries</span></div>
  </div>
</section>

<section class="card card--back" aria-label="Card back">
  <div class="wordmark">
    <div class="wordmark__dot"></div>
    <div class="wordmark__name"><span>Flowbend</span><span>Industries</span></div>
  </div>

  <div class="card__divider"></div>

  <div class="contact">
    <h1 class="contact__name">Glen Marsh</h1>
    <p class="contact__role">Director</p>
    <ul class="contact__list">
      <li class="contact__item">
        <svg class="contact__icon" viewBox="0 0 24 24"><path d="M6.6 10.8a15.1 15.1 0 0 0 6.6 6.6l2.2-2.2a1 1 0 0 1 1-.25 11.4 11.4 0 0 0 3.6.57 1 1 0 0 1 1 1V20a1 1 0 0 1-1 1A17 17 0 0 1 3 4a1 1 0 0 1 1-1h3.5a1 1 0 0 1 1 1c0 1.25.2 2.45.57 3.57a1 1 0 0 1-.25 1z"/></svg>
        0438 760 514
      </li>
      <li class="contact__item">
        <svg class="contact__icon" viewBox="0 0 24 24"><path d="M2 5h20v14H2z M3 6l9 7 9-7" fill="var(--brand-blue)" stroke="#fff" stroke-width="1.5"/></svg>
        Sales@flowbend.com.au
      </li>
      <li class="contact__item contact__item--plain">17 Dorwell St</li>
      <li class="contact__item contact__item--plain">Kelbrook NSW 2715</li>
    </ul>
  </div>

  <svg class="bands" viewBox="0 0 700 90" preserveAspectRatio="none" aria-hidden="true">
    <polygon points="0,70 440,20 440,90 0,90" fill="var(--brand-green)"/>
    <polygon points="0,76 440,30 440,90 0,90" fill="var(--brand-green-dark)"/>
    <polygon points="430,0 700,0 700,90 430,90" fill="var(--brand-blue)"/>
    <polygon points="430,0 440,0 440,90 430,90" fill="var(--brand-blue-dark)"/>
  </svg>
  <p class="website">www.flowbend.com.au</p>
</section>

</body>
</html>
```